Bring me business with this creative business card

Design my new business card. I am looking for something different with an impact. People will take a look at this card & they will 1- see how different & creative I am, 2-understand what I do 3- Call me to meet me!

I make videos with a message, testimonials. I am dynamic, fun, creative & human. My new website is in construction but in the meantime you can check this old one: brightpath.ca & another one Tidebloom.com & tidebloom facebook page.
I make videos. sometimes with a cameraman, sometimes with my phone. As an ex Public Relations agent, the message is the most important thing for me. I want to make my clients shine! When they start with me they often remind me of a lamb, when I finish coaching them they are powerful like LIONS! That's why I need a powerful business card!

Target Market(s)

Entrepreneurs, solo entrepreneurs, small & medium companies & start ups. People i will meet while networking. People that need videos on their website & social Networks to get attention, to be visible. men & women. From 35 to 49 years old.
I am an ex Public relations agent. I used to send clients in traditional medias, now with videos they have more chances to be seen on google the new media. I do videos of the president, his team, his loyal clients saying how great the company is & expert videos like series so people can be seen for example every 1 st of every month with a short 2 minute video. Also with my 20 years in marketing & communications I can coach & give tips to anybody who needs it.
Target: anybody who would like my old website brightpath.ca & I also have another website but it will be off line soon: tidebloom.com could give you ideas.

Industry/Entity Type

Communications

Contact Information for Business Card

I am in Montreal,So the business cards have to be the usual size like we have in Montreal: 9 cm x 5 cm
Details:My text: Mathilde Tessier Communication coach/Chief Spark. "Crafting Stories that sound like you" off: 514-555-0147 cell: 514-555-0183. tidebloom.com
mathilde@tidebloom.com logo facebook, youtube, instagram

Colors
f37122

Requirements
Must have
• Dynamic, happy. Orange. Be creative in the look but NOT the shape of the card. Easy to read. Big enough to read.
Should not have
• No funny shapes: no round, no square, just the usual. I love creative but NOT on shape.

```html
<!DOCTYPE html>
<html lang="en">
<head>
<meta charset="utf-8">
<title>Tidebloom Business Card</title>
<link href="https://fonts.googleapis.com/css2?family=Roboto:wght@400;500&family=Roboto+Condensed:wght@500&family=Cinzel:wght@600&display=swap" rel="stylesheet">
<style>
  :root {
    --backdrop: #2a2a2a;
    --orange: #e85c24;
    --orange-bright: #f37122;
    --amber: #f5a01c;
    --paper: #f4f4f4;
    --white: #ffffff;
  }
  * { margin: 0; padding: 0; box-sizing: border-box; }
  html, body {
    width: 1200px; height: 960px; overflow: hidden;
    background: var(--backdrop);
  }
  .canvas { position: relative; width: 1200px; height: 960px; }
  .card {
    position: absolute; width: 600px; height: 342px;
    background: var(--paper); overflow: hidden;
  }
  .card-front { left: 314px; top: 113px; }
  .card-back { left: 311px; top: 472px; }

  .front-panel {
    position: absolute; left: 0; top: 0; width: 430px; height: 100%;
    background: var(--orange);
  }
  .front-accent {
    position: absolute; left: 306px; top: -4px; width: 282px; height: 346px;
    border: 3px solid var(--white); border-radius: 60px 60px 90px 90px;
    background: linear-gradient(160deg, var(--amber), var(--orange-bright));
  }
  .identity { position: absolute; left: 48px; top: 62px; color: var(--white); }
  .identity-name {
    font-family: "Roboto Condensed", sans-serif; font-weight: 500;
    font-size: 22px; letter-spacing: 0.3px; line-height: 26px;
  }
  .identity-role {
    font-family: "Roboto", sans-serif; font-weight: 400;
    font-size: 15px; line-height: 19px; text-transform: uppercase;
  }
  .identity-name + .identity-role { margin-top: 3px; }
  .contact-list {
    position: absolute; left: 48px; top: 217px; list-style: none;
    font-family: "Roboto", sans-serif; font-size: 14px; color: var(--white);
  }
  .contact-list li { display: flex; align-items: center; height: 19px; }
  .contact-list svg { width: 14px; height: 14px; margin-right: 9px; fill: var(--white); }

  .back-content {
    position: absolute; left: 0; top: 0; width: 100%; height: 100%;
    display: flex; flex-direction: column; align-items: center;
  }
  .brand-dot {
    width: 100px; height: 100px; border-radius: 50%;
    background: var(--orange-bright); margin-top: 62px;
  }
  .brand-name {
    font-family: "Cinzel", serif; font-weight: 600; font-size: 32px;
    color: var(--orange); letter-spacing: 1px; margin-top: 34px; line-height: 38px;
  }
  .brand-motto {
    display: flex; align-items: center; gap: 8px;
    font-family: "Roboto", sans-serif; font-size: 13px; color: var(--amber);
    letter-spacing: 0.5px; line-height: 16px;
  }
  .brand-motto::before, .brand-motto::after {
    content: ""; width: 32px; height: 1px; background: var(--amber);
  }
  .brand-tagline {
    font-family: "Roboto", sans-serif; font-weight: 500; font-size: 14px;
    color: var(--orange); margin-top: 2px; line-height: 18px;
  }
  .social-row {
    position: absolute; left: 170px; top: 296px; width: 260px;
    display: flex; align-items: center; gap: 5px;
  }
  .social-rule { flex: 1; height: 1px; background: var(--orange); }
  .social-dot { width: 24px; height: 24px; border-radius: 50%; background: var(--orange); }
</style>
</head>
<body>
<main class="canvas">
  <section class="card card-front">
    <div class="front-panel"></div>
    <div class="front-accent" role="img" aria-label="Large brand emblem area in orange and amber tones"></div>
    <div class="identity">
      <p class="identity-name">MATHILDE T.</p>
      <p class="identity-role">Communication Coach</p>
      <p class="identity-role">Chief Spark</p>
    </div>
    <ul class="contact-list">
      <li><svg viewBox="0 0 24 24"><path d="M6.6 10.8a15 15 0 0 0 6.6 6.6l2.2-2.2c.3-.3.7-.4 1-.2 1.1.4 2.3.6 3.6.6.6 0 1 .4 1 1V20c0 .6-.4 1-1 1A17 17 0 0 1 3 4c0-.6.4-1 1-1h3.5c.6 0 1 .4 1 1 0 1.3.2 2.5.6 3.6.1.3 0 .7-.2 1z"/></svg>514-555-0147</li>
      <li><svg viewBox="0 0 24 24"><path d="M7 1h10a2 2 0 0 1 2 2v18a2 2 0 0 1-2 2H7a2 2 0 0 1-2-2V3a2 2 0 0 1 2-2zm0 3v14h10V4z"/></svg>514-555-0183</li>
      <li><svg viewBox="0 0 24 24"><path d="M2 5h20v14H2zm2 2v.5l8 5 8-5V7zm0 2.8V17h16V9.8l-8 5z"/></svg>mathilde@tidebloom.com</li>
      <li><svg viewBox="0 0 24 24"><path d="M12 2a10 10 0 1 0 0 20 10 10 0 0 0 0-20zm-1 17.9A8 8 0 0 1 4.2 10L9 15v1a2 2 0 0 0 2 2zm6.9-2.5A2 2 0 0 0 16 16h-1v-3a1 1 0 0 0-1-1H8v-2h2a1 1 0 0 0 1-1V7h2a2 2 0 0 0 2-2v-.4a8 8 0 0 1 2.9 12.8z"/></svg>www.tidebloom.com</li>
    </ul>
  </section>

  <section class="card card-back">
    <div class="back-content">
      <div class="brand-dot"></div>
      <p class="brand-name">TIDEBLOOM</p>
      <p class="brand-motto">1 STORY 1 VOICE</p>
      <p class="brand-tagline">Crafting Stories that sound like you</p>
    </div>
    <div class="social-row">
      <span class="social-rule"></span>
      <span class="social-dot"></span>
      <span class="social-dot"></span>
      <span class="social-dot"></span>
      <span class="social-rule"></span>
    </div>
  </section>
</main>
</body>
</html>
```